Measuring Card for Eyelash Extensions

I want this made for my brand and in a format that I can get printed on standard size business cards (3.5 x 2 inches). The measurement must be accurate to the end of the business card because this will be put up to the eye to measure the lash length.
This is being sent to lash extension artists so they can measure the natural lash before they begin applying eyelash extensions. I want it to look like the card I attached and it must be an accurate measurement.

Target Market(s)

Lash Extension Artists

Font styles to use
Sans Serif

Colors
ffffff

Requirements
Must have
• Must be accurate measurement on a 3.5 x 2 inch business card.
Nice to have
• To look very similar to the card in the photo I attached.

```html
<!DOCTYPE html>
<html lang="en">
<head>
<meta charset="utf-8">
<title>Velora Beauty – Lash Length Measuring Card</title>
<link href="https://fonts.googleapis.com/css2?family=Open+Sans:wght@400;600;700&display=swap" rel="stylesheet">
<style>
  :root {
    --stage: #e9e9eb;
    --card: #ffffff;
    --violet: #2e1472;
    --tan: #c9a48a;
    --ink: #2e1472;
    --guide: #e2dcd6;
    --photo-a: #c9c3bd;
    --photo-b: #7d736c;
  }
  * { box-sizing: border-box; margin: 0; padding: 0; }
  html, body { width: 1200px; height: 797px; overflow: hidden; }
  body {
    background: var(--stage);
    font-family: "Open Sans", Arial, sans-serif;
    position: relative;
  }
  .card {
    position: absolute;
    left: 394px; top: 38px;
    width: 412px; height: 720px;
    background: var(--card);
    overflow: hidden;
  }
  .title-block {
    position: absolute; left: 0; top: 0;
    width: 178px; height: 112px;
    background: var(--violet);
    color: #fff;
    display: flex; flex-direction: column; justify-content: center; align-items: center;
    font-weight: 700; font-size: 18px; line-height: 1.15; letter-spacing: 0.06em;
    text-align: center;
  }
  .wordmark {
    position: absolute; left: 22px; top: 128px;
    font-weight: 600; font-size: 44px; letter-spacing: 0.04em;
    color: var(--violet); line-height: 1;
  }
  .tagline {
    position: absolute; left: 24px; top: 184px;
    font-size: 10.5px; letter-spacing: 0.14em; color: var(--tan);
  }
  .lash-photo {
    position: absolute; left: 22px; top: 222px;
    width: 132px; height: 128px;
    background: linear-gradient(135deg, var(--photo-a), var(--photo-b));
  }
  .safe-lengths {
    position: absolute; left: 172px; top: 222px; width: 222px;
  }
  .label {
    display: inline-block;
    border-left: 6px solid var(--tan);
    padding-left: 8px;
    font-weight: 700; font-size: 16px; letter-spacing: 0.06em;
    color: var(--tan); margin-bottom: 8px;
  }
  .body-text { font-size: 15.5px; line-height: 1.35; color: var(--ink); }
  .guides {
    position: absolute; left: 0; top: 378px; width: 100%;
  }
  .guide { border-top: 1px dashed var(--guide); height: 0; }
  .example {
    position: absolute; left: 172px; top: 396px; width: 222px;
  }
  .example .body-text + .body-text { margin-top: 6px; }
  .emphasis { font-weight: 700; text-decoration: underline; }
  .ruler { position: absolute; left: 0; top: 600px; }
</style>
</head>
<body>
  <main class="card" aria-label="Lash length measuring card">
    <div class="title-block"><span>MEASURE</span><span>LASH</span><span>LENGTH</span></div>

    <div class="wordmark">VELORA BEAUTY</div>
    <div class="tagline">TOOLS FOR LASH ARTISTS</div>

    <div class="lash-photo" role="img" aria-label="Close-up photo of natural lashes against a millimetre ruler"></div>

    <section class="safe-lengths">
      <div class="label">SAFE LENGTHS</div>
      <p class="body-text">Never use extensions that are longer than +3mm from natural lashes. Never go +1mm on the inners.</p>
    </section>

    <div class="guides"><div class="guide"></div></div>

    <section class="example">
      <div class="label">EXAMPLE</div>
      <p class="body-text">Natural lash<br>= 9mm</p>
      <p class="body-text">Use <span class="emphasis">MAXIMUM</span><br>= 12mm</p>
    </section>

    <svg class="ruler" width="412" height="80" viewBox="0 0 412 80" aria-label="Millimetre ruler, 0 to 20 mm from the card edge">
      <g stroke="#2e1472" stroke-width="1">
        <line x1="0" y1="1" x2="162" y2="1"/>
        <line x1="0.5" y1="1" x2="0.5" y2="22"/>
        <line x1="8.1" y1="1" x2="8.1" y2="10"/>
        <line x1="16.2" y1="1" x2="16.2" y2="10"/>
        <line x1="24.3" y1="1" x2="24.3" y2="10"/>
        <line x1="32.4" y1="1" x2="32.4" y2="10"/>
        <line x1="40.5" y1="1" x2="40.5" y2="18"/>
        <line x1="48.6" y1="1" x2="48.6" y2="10"/>
        <line x1="56.7" y1="1" x2="56.7" y2="10"/>
        <line x1="64.8" y1="1" x2="64.8" y2="10"/>
        <line x1="72.9" y1="1" x2="72.9" y2="10"/>
        <line x1="81" y1="1" x2="81" y2="22"/>
        <line x1="89.1" y1="1" x2="89.1" y2="10"/>
        <line x1="97.2" y1="1" x2="97.2" y2="10"/>
        <line x1="105.3" y1="1" x2="105.3" y2="10"/>
        <line x1="113.4" y1="1" x2="113.4" y2="10"/>
        <line x1="121.5" y1="1" x2="121.5" y2="18"/>
        <line x1="129.6" y1="1" x2="129.6" y2="10"/>
        <line x1="137.7" y1="1" x2="137.7" y2="10"/>
        <line x1="145.8" y1="1" x2="145.8" y2="10"/>
        <line x1="153.9" y1="1" x2="153.9" y2="10"/>
        <line x1="161.5" y1="1" x2="161.5" y2="22"/>
      </g>
      <g fill="#c9a48a" font-family="Open Sans, Arial, sans-serif" font-size="11" font-weight="600">
        <text transform="translate(44.5 26) rotate(90)">5 mm</text>
        <text transform="translate(85 28) rotate(90)">10 mm</text>
        <text transform="translate(125.5 26) rotate(90)">15 mm</text>
        <text transform="translate(165.5 28) rotate(90)">20 mm</text>
      </g>
    </svg>
  </main>
</body>
</html>
```